6"x9" Postcard Mailer

A 6"x9" Postcard mailer targeted to forensic laboratories to advertise or mock forensic samples (https://veltrascience.example/products/mock-forensic-samples/).

Here is some copy, but we can modify if there is not enough space:

Headline:
Expedite Training, Validation, & R&D with Our Ready-to-Use Mock Samples

Bullet Points:

- Wide Variety of Sample Types: IRB-approved samples mimicking crime scene substances, including semen, hair, bone, saliva, blood, and vaginal epithelial cells.
- Diverse Scenarios: Simulate sexual assault and degraded samples for varied conditions.
- Custom Solutions: Tailored DNA quantities and concentrations to suit your lab's needs.

Use discount code TRAL47 for a 10% discount

```html
<!DOCTYPE html>
<html lang="en">
<head>
<meta charset="utf-8">
<title>Veltra Science – Mock Forensic Samples Postcard</title>
<link href="https://fonts.googleapis.com/css2?family=Poppins:wght@400;500;600;700&family=Oswald:wght@500&display=swap" rel="stylesheet">
<style>
  :root {
    --navy: #2b57a8;
    --sky: #2f8fd3;
    --ink: #3a3d44;
    --panel: #e9eaed;
    --white: #ffffff;
    --page: #ffffff;
  }
  * { box-sizing: border-box; margin: 0; padding: 0; }
  html, body { width: 1200px; height: 2307px; overflow: hidden; background: var(--page); }
  body { position: relative; font-family: "Poppins", sans-serif; color: var(--ink); }

  .postcard {
    position: absolute; left: 100px; width: 1000px; height: 667px;
    background: var(--white); overflow: hidden;
    box-shadow: 0 14px 28px rgba(0,0,0,.22);
  }
  .postcard--front { top: 366px; }
  .postcard--back { top: 1273px; }
  .postcard__art { position: absolute; inset: 0; width: 1000px; height: 667px; }

  .brand-name {
    position: absolute; font-family: "Poppins", sans-serif; font-weight: 500;
    color: var(--navy); letter-spacing: -0.5px; white-space: nowrap;
  }
  .postcard--front .brand-name { left: 45px; top: 40px; font-size: 48px; }
  .postcard--back .brand-name { left: 585px; top: 52px; font-size: 24px; }

  .headline {
    position: absolute; left: 42px; top: 158px; color: var(--white);
    font-weight: 700; font-size: 41px; line-height: 1.0; letter-spacing: .3px;
  }
  .subhead {
    position: absolute; left: 47px; top: 284px; color: var(--white);
    font-weight: 600; font-size: 28px; line-height: 1.05;
  }
  .offer { position: absolute; left: 38px; top: 408px; }
  .offer__row { display: flex; align-items: center; gap: 10px; }
  .offer__label {
    font-family: "Oswald", sans-serif; font-weight: 500; font-size: 25px;
    color: var(--ink); border-top: 2px dotted #b9bcc2; border-bottom: 2px dotted #b9bcc2;
    padding: 4px 0; line-height: 1;
  }
  .offer__code {
    border: 2px solid var(--navy); color: var(--navy); font-weight: 700;
    font-size: 48px; line-height: 1; padding: 4px 10px 2px;
  }
  .offer__line { margin-top: 10px; font-size: 40px; line-height: 1; color: #2c2f36; }
  .offer__line strong { color: var(--sky); font-weight: 700; }

  .contact { position: absolute; left: 38px; }
  .postcard--front .contact { top: 568px; }
  .postcard--back .contact { top: 570px; }
  .contact__phone {
    display: flex; align-items: center; gap: 12px; font-weight: 600;
    font-size: 41px; line-height: 1; color: var(--navy);
  }
  .postcard--back .contact__phone { color: var(--white); }
  .contact__web { display: flex; align-items: center; gap: 12px; margin-top: 8px; }
  .contact__url {
    background: var(--sky); color: var(--white); font-size: 19px; font-weight: 500;
    letter-spacing: 3.5px; padding: 0 10px; line-height: 25px;
    border-right: 3px solid var(--sky); box-shadow: 5px 0 0 var(--white), 8px 0 0 var(--sky);
  }
  .icon { flex: none; }

  .features { position: absolute; left: 40px; top: 55px; width: 420px; }
  .feature { position: absolute; left: 0; display: flex; gap: 24px; }
  .feature__icon {
    width: 78px; height: 72px; background: var(--navy); border-radius: 4px;
    display: flex; align-items: center; justify-content: center; flex: none;
    box-shadow: inset 0 0 0 3px #4f79c6;
  }
  .feature__title {
    color: var(--sky); font-weight: 700; font-size: 22px; line-height: 1;
    text-transform: uppercase; margin-bottom: 5px;
  }
  .feature__text { font-size: 17px; line-height: 1.15; color: var(--ink); }
  .feature--types { top: 0; }
  .feature--scenarios { top: 172px; }
  .feature--custom { top: 322px; }

  .stamp-box {
    position: absolute; left: 850px; top: 27px; width: 105px; height: 103px;
    border: 2px solid #b8babe;
  }
</style>
</head>
<body>

<!-- FRONT -->
<section class="postcard postcard--front" aria-label="Postcard front">
  <svg class="postcard__art" viewBox="0 0 1000 667" aria-hidden="false">
    <defs>
      <linearGradient id="photoTone" x1="0" y1="0" x2="0.2" y2="1">
        <stop offset="0" stop-color="#141821"/>
        <stop offset="0.3" stop-color="#3e4656"/>
        <stop offset="0.5" stop-color="#2f5fc4"/>
        <stop offset="0.78" stop-color="#c9ced8"/>
        <stop offset="1" stop-color="#eef0f3"/>
      </linearGradient>
    </defs>
    <path class="band band--navy" fill="var(--navy)" d="M0,142 C180,128 380,158 610,138 V272 H0 Z"/>
    <path class="band band--sky" fill="var(--sky)" d="M0,272 H610 V350 C430,385 200,388 0,372 Z"/>
    <path class="band band--contact" fill="var(--panel)" d="M0,545 C220,528 420,555 610,538 V667 H0 Z"/>
    <path class="photo-edge" fill="none" stroke="var(--sky)" stroke-width="12"
      d="M489,0 C494,70 584,90 582,150 C580,215 484,230 484,300 C484,380 584,410 582,470 C580,540 484,560 489,667"/>
    <path class="photo" role="img" aria-label="Photo: gloved hands lifting a blood sample with a swab from a white cloth, beside a ring"
      fill="url(#photoTone)"
      d="M495,0 C500,70 590,90 588,150 C586,215 490,230 490,300 C490,380 590,410 588,470 C586,540 490,560 495,667 H1000 V0 Z"/>
  </svg>

  <div class="brand-name">Veltra Science</div>
  <h1 class="headline">EXPEDITE TRAINING,<br>VALIDATION, &amp; R&amp;D</h1>
  <p class="subhead">WITH OUR READY-TO-USE<br>MOCK SAMPLES</p>

  <div class="offer">
    <div class="offer__row">
      <span class="offer__label">USE DISCOUNT CODE</span>
      <span class="offer__code">TRAL47</span>
    </div>
    <p class="offer__line">FOR A <strong>DISCOUNT 10%</strong></p>
  </div>

  <div class="contact">
    <div class="contact__phone">
      <svg class="icon" width="34" height="34" viewBox="0 0 34 34"><rect width="34" height="34" rx="8" fill="var(--navy)"/><path d="M11 8 L15 12 L12.5 15 C14 18.5 16 20.5 19 21.5 L22 19 L26 23 L23 26.5 C15 26 8.5 19.5 7.5 11.5 Z" fill="#fff"/></svg>
      +1 555 014 2387
    </div>
    <div class="contact__web">
      <svg class="icon" width="24" height="24" viewBox="0 0 24 24"><circle cx="12" cy="12" r="10" fill="none" stroke="var(--sky)" stroke-width="2.2"/><path d="M2 12 H22 M12 2 C6 8 6 16 12 22 M12 2 C18 8 18 16 12 22" fill="none" stroke="var(--sky)" stroke-width="2"/></svg>
      <span class="contact__url">WWW.VELTRASCIENCE.EXAMPLE</span>
    </div>
  </div>
</section>

<!-- BACK -->
<section class="postcard postcard--back" aria-label="Postcard back">
  <svg class="postcard__art" viewBox="0 0 1000 667">
    <defs>
      <linearGradient id="kitTone" x1="0" y1="0" x2="1" y2="1">
        <stop offset="0" stop-color="#f3f5f8"/>
        <stop offset="0.55" stop-color="#3d6fcf"/>
        <stop offset="1" stop-color="#1f4da6"/>
      </linearGradient>
    </defs>
    <path class="panel" fill="var(--panel)" d="M0,0 H550 C545,70 450,110 455,175 L455,470 C455,510 540,520 550,667 H0 Z"/>
    <path fill="none" stroke="var(--sky)" stroke-width="10" d="M550,0 C545,70 450,110 455,175"/>
    <path class="band band--contact-dark" fill="var(--navy)" d="M0,548 C200,536 380,546 465,538 C520,540 545,600 550,667 H0 Z"/>
    <path fill="none" stroke="var(--sky)" stroke-width="10" d="M455,470 C455,510 540,520 550,667"/>
    <g class="dividers" stroke="#3a3d44" stroke-width="1.5">
      <line x1="40" y1="204" x2="365" y2="204"/>
      <line x1="365" y1="204" x2="430" y2="204" stroke-dasharray="2 2"/>
      <line x1="40" y1="353" x2="105" y2="353" stroke-dasharray="2 2"/>
      <line x1="105" y1="353" x2="420" y2="353"/>
      <line x1="40" y1="503" x2="365" y2="503"/>
      <line x1="365" y1="503" x2="430" y2="503" stroke-dasharray="2 2"/>
    </g>
    <circle cx="515" cy="330" r="120" fill="var(--white)" stroke="var(--navy)" stroke-width="10"/>
    <circle cx="515" cy="330" r="104" fill="url(#kitTone)" role="img" aria-label="Product photo: open mock sample kit box with vials"/>
  </svg>

  <div class="features">
    <div class="feature feature--types">
      <div class="feature__icon">
        <svg width="40" height="44" viewBox="0 0 40 44"><path d="M13 4 H27 M15 4 V18 L8 34 A6 6 0 0 0 14 42 H26 A6 6 0 0 0 32 34 L25 18 V4" fill="none" stroke="#fff" stroke-width="3" stroke-linejoin="round"/><path d="M14 32 C14 28 18 26 18 22 C18 26 22 28 22 32 A4 4 0 0 1 14 32 Z" fill="#fff"/></svg>
      </div>
      <div>
        <h2 class="feature__title">Wide Variety of<br>Sample Types</h2>
        <p class="feature__text">IRB-approved samples mimicking crime scene substances, including semen, hair, bone, saliva, blood, and vaginal epithelial cells.</p>
      </div>
    </div>
    <div class="feature feature--scenarios">
      <div class="feature__icon">
        <svg width="46" height="46" viewBox="0 0 46 46"><circle cx="23" cy="23" r="11" fill="none" stroke="#fff" stroke-width="3"/><g fill="#fff"><circle cx="23" cy="6" r="4.5"/><circle cx="23" cy="40" r="4.5"/><circle cx="6" cy="23" r="4.5"/><circle cx="40" cy="23" r="4.5"/></g></svg>
      </div>
      <div>
        <h2 class="feature__title">Diverse<br>Scenarios</h2>
        <p class="feature__text">Simulate sexual assault and degraded samples for varied conditions.</p>
      </div>
    </div>
    <div class="feature feature--custom">
      <div class="feature__icon">
        <svg width="36" height="46" viewBox="0 0 36 46"><path d="M4 3 H32 M4 43 H32 M8 3 C8 16 28 30 28 43 M28 3 C28 16 8 30 8 43" fill="none" stroke="#fff" stroke-width="3"/><path d="M11 14 H25 M11 32 H25" stroke="#fff" stroke-width="2"/></svg>
      </div>
      <div>
        <h2 class="feature__title">Custom<br>Solutions</h2>
        <p class="feature__text">Tailored DNA quantities and concentrations to suit your lab's needs.</p>
      </div>
    </div>
  </div>

  <div class="contact">
    <div class="contact__phone">
      <svg class="icon" width="30" height="30" viewBox="0 0 34 34"><path d="M11 8 L15 12 L12.5 15 C14 18.5 16 20.5 19 21.5 L22 19 L26 23 L23 26.5 C15 26 8.5 19.5 7.5 11.5 Z" fill="#fff"/></svg>
      +1 555 014 2387
    </div>
    <div class="contact__web">
      <svg class="icon" width="24" height="24" viewBox="0 0 24 24"><circle cx="12" cy="12" r="10" fill="none" stroke="var(--sky)" stroke-width="2.2"/><path d="M2 12 H22 M12 2 C6 8 6 16 12 22 M12 2 C18 8 18 16 12 22" fill="none" stroke="var(--sky)" stroke-width="2"/></svg>
      <span class="contact__url">WWW.VELTRASCIENCE.EXAMPLE</span>
    </div>
  </div>

  <div class="brand-name">Veltra Science</div>
  <div class="stamp-box" aria-label="Stamp area"></div>
</section>

</body>
</html>
```